Larkmoor Drones Business Card

We are a new company based in Central Queensland, Australia that uses specalised drones (Voskel Ferra Q80) to undertake mainly agricultural operations, like spraying weeds, spraying crops, spreading seed etc. I have attached a Plimbo proof of a card I was thinking along the lines of - purely a start point. The drone used in the business card MUST be a Voskel Ferra Q80.
I am very open to other ideas, especially fonts and layout. I don't have website etc set up yet.
The images are stock and easily interchangeable, I just ask that any background images reflect the local central Queensland area. The photo of the drone is not even complete (propellers cut off) and I need a new stock photo – I’m not sure if this is an issue, or I can pay for an image if need be. PLEASE FIND AN FERRA Q80 image - 4 sprayers, not 6.
The logo/business name is very draft and looking for further ideas, ideally incorporating drones or agriculture design elements into the design of the business name. The business name needs work on the graphic/design – it is a draft that I have included, the drone propellers (being a different colour) are DRAFT only and intended for changes. PLEASE DO NOT USE THE DRONE PORPELLER I HAVE USED AS A DRAFT. TRY TO FIND SOMETHING ELSE.. The arrow is a shape and not aligned in any way, I would also like ideas on different fonts and additional elements, like air streams, aviation elements, aviation or country western (farming like) themes and fonts etc.
Ideally looking at staying within the blue, green and yellow colours, keeping with an natural, outdoorsy, environmental feel.

Target Market(s)

Farmers, Agriculture, Local Governments, Land Managers

Industry/Entity Type

Agriculture, Drones, Aviation

Contact Information for Business Card

Agricultural Drone (Voskel Ferra Q80), Farming, Business Name.

Font styles to use
Sans Serif

Colors
0054AA
0677BA
7BADD7
CADEEF
E8F1F8
0094D4
00A9DD
6FCCEA
C7EBF8
E9F6FB
00AB8E
00BBA5
67D7C9
C6EFE9
E9F9F6
59FF00
82FF00
B8FF75
E3FFCB
F4FFEA

Requirements
Must have
• Voskel Ferra Q80 Drone
Should not have
• Tractors

```html
<!DOCTYPE html>
<html lang="en">
<head>
<meta charset="utf-8">
<title>Larkmoor Drones Business Card</title>
<link rel="stylesheet" href="https://fonts.googleapis.com/css2?family=Cinzel:wght@500&family=Alegreya:wght@700;800&family=Poppins:wght@400;700&display=swap">
<style>
  :root {
    --page: #b9b9bb;
    --sky-top: #7bade7;
    --sky-mid: #cadeef;
    --haze: #eef0e4;
    --grass-light: #7fa84a;
    --grass: #4f8a2a;
    --grass-deep: #3a6f1c;
    --band-green: #5f8f45;
    --logo-green: #3f6f1e;
    --drone-dark: #4a4f52;
    --drone-mid: rgba(74, 79, 82, 0.55);
    --mist: rgba(236, 226, 190, 0.7);
    --white: #ffffff;
    --dot-yellow: #f2e600;
  }
  * { box-sizing: border-box; margin: 0; padding: 0; }
  html, body { width: 1200px; height: 900px; overflow: hidden; }
  body {
    background: var(--page);
    display: flex;
    flex-direction: column;
    align-items: center;
    justify-content: center;
    gap: 36px;
  }
  .card {
    position: relative;
    width: 700px;
    height: 400px;
    border-radius: 34px;
    overflow: hidden;
    box-shadow: 0 8px 18px rgba(0,0,0,0.25);
  }
  .card__photo {
    position: absolute;
    inset: 0;
    background:
      linear-gradient(180deg, var(--sky-top) 0%, var(--sky-mid) 32%, var(--haze) 48%, var(--grass-light) 60%, var(--grass) 78%, var(--grass-deep) 100%);
  }
  .card__drone {
    position: absolute;
    width: 200px;
    height: 110px;
    border-radius: 50%;
    background:
      radial-gradient(ellipse at 50% 40%, var(--drone-dark) 0%, var(--drone-mid) 38%, rgba(74,79,82,0) 62%),
      radial-gradient(ellipse at 45% 95%, var(--mist) 0%, rgba(236,226,190,0) 60%);
  }
  .card--front .card__drone { left: 372px; top: 100px; }
  .card--back .card__drone { left: 392px; top: 110px; }
  .card__band {
    position: absolute;
    inset: 0;
    width: 100%;
    height: 100%;
  }
  .wordmark {
    position: absolute;
    font-family: "Cinzel", serif;
    font-weight: 500;
    line-height: 0.95;
    letter-spacing: 1px;
  }
  .wordmark span { display: block; }
  .wordmark span + span { padding-left: 54px; }
  .card--front .wordmark { left: 44px; top: 70px; font-size: 54px; color: var(--white); }
  .card--back .wordmark { left: 44px; top: 60px; font-size: 58px; color: var(--logo-green); }

  .service-area {
    position: absolute;
    left: 60px;
    top: 218px;
    font-family: "Alegreya", serif;
    font-weight: 700;
    font-size: 17px;
    letter-spacing: 1px;
    color: var(--white);
    text-transform: uppercase;
  }
  .services {
    position: absolute;
    left: 84px;
    top: 252px;
    list-style: none;
    font-family: "Alegreya", serif;
    font-weight: 800;
    font-size: 27px;
    line-height: 1.15;
    color: var(--white);
  }
  .services li::before {
    content: "";
    display: inline-block;
    width: 7px;
    height: 7px;
    border-radius: 50%;
    background: var(--dot-yellow);
    margin-right: 8px;
    vertical-align: middle;
  }

  .person {
    position: absolute;
    left: 60px;
    top: 212px;
    font-family: "Poppins", sans-serif;
    color: var(--white);
  }
  .person__name { font-weight: 700; font-size: 30px; letter-spacing: 0.5px; line-height: 1.05; }
  .person__role { font-weight: 400; font-size: 21px; line-height: 1.2; }
  .contacts {
    list-style: none;
    margin-top: 14px;
    font-size: 22px;
    line-height: 1.35;
  }
  .contacts li { display: flex; align-items: center; gap: 10px; }
  .contacts svg { width: 20px; height: 20px; flex: none; }
</style>
</head>
<body>

  <section class="card card--front" aria-label="Business card front">
    <div class="card__photo" role="img" aria-label="Photo of a green Central Queensland paddock with a tree line and hills under a morning sky"></div>
    <div class="card__drone" role="img" aria-label="Photo of a Voskel Ferra Q80 agricultural drone with four sprayers misting the paddock"></div>
    <svg class="card__band" viewBox="0 0 700 400" preserveAspectRatio="none" aria-hidden="true">
      <path d="M460 0 H700 V260 C640 220 600 150 560 90 C530 45 500 15 460 0 Z" fill="var(--band-green)"/>
    </svg>
    <h1 class="wordmark"><span>Larkmoor</span><span>Drones</span></h1>
    <p class="service-area">Servicing Central Queensland</p>
    <ul class="services">
      <li>Spraying Weeds</li>
      <li>Spraying Crops</li>
      <li>Spreading Seeds</li>
    </ul>
  </section>

  <section class="card card--back" aria-label="Business card back">
    <div class="card__photo" role="img" aria-label="Photo of a green Central Queensland paddock with a tree line and hills under a morning sky"></div>
    <div class="card__drone" role="img" aria-label="Photo of a Voskel Ferra Q80 agricultural drone with four sprayers misting the paddock"></div>
    <svg class="card__band" viewBox="0 0 700 400" preserveAspectRatio="none" aria-hidden="true">
      <path d="M460 0 H700 V260 C640 220 600 150 560 90 C530 45 500 15 460 0 Z" fill="var(--band-green)"/>
    </svg>
    <h2 class="wordmark"><span>Larkmoor</span><span>Drones</span></h2>
    <div class="person">
      <p class="person__name">MARCUS HOLLOWAY</p>
      <p class="person__role">Managing Director</p>
      <ul class="contacts">
        <li>
          <svg viewBox="0 0 24 24" aria-hidden="true"><path fill="var(--white)" d="M6.6 10.8a15 15 0 0 0 6.6 6.6l2.2-2.2a1 1 0 0 1 1-.25 11.4 11.4 0 0 0 3.6.57 1 1 0 0 1 1 1V20a1 1 0 0 1-1 1A17 17 0 0 1 3 4a1 1 0 0 1 1-1h3.5a1 1 0 0 1 1 1c0 1.25.2 2.45.57 3.57a1 1 0 0 1-.25 1z"/></svg>
          044-318 402 776
        </li>
        <li>
          <svg viewBox="0 0 24 24" aria-hidden="true"><rect x="2" y="5" width="20" height="14" rx="1.5" fill="var(--white)"/><path d="M3 6l9 7 9-7" fill="none" stroke="var(--grass)" stroke-width="1.8"/></svg>
          info@larkmoor.example
        </li>
        <li>
          <svg viewBox="0 0 24 24" aria-hidden="true"><circle cx="12" cy="12" r="9" fill="none" stroke="var(--white)" stroke-width="2"/><path d="M3 12h18M12 3c3 3 3 15 0 18M12 3c-3 3-3 15 0 18" fill="none" stroke="var(--white)" stroke-width="1.6"/></svg>
          www.larkmoor.example
        </li>
      </ul>
    </div>
  </section>

</body>
</html>
```